Valdo Capital

We need a corporate style website design for a new company based in Shenzhen's Qianhai Special Economic Development Zone, China. We provide a range of financial services to large international investment companies. Typically these companies invest over 5 million RMB. The company is part of a group that consists of NorthKilns, ValdoTrusts and ValdoEquity. Our location and gateway into Qianhai Special Economic Zone is our core advantage. We would like to see designs that Do Not use purple and orange. The website design should be similar to other websites in this family but different enough to give it a unique style (See attached website links for reference). The final design should communicate financial safety and growth. This website will act partly as a business chamber with connections to the government so we would like it to be diplomatic in style.

www.northkilns.example
www.valdotrusts.example

*Nevegation Bar
Should including Homepage, Financial Product, Team, News.
Could refer to www.valdotrusts.example

*Contact Details

Miss Lan
Address:E 728, North Block, KMO Centre, East Sector, Shenzhen Bright Science Campus
Telephone: +86 0755 63920417
Cellphone: +86 13957280316

* Social Media
Should be grouped like:
1. Weibo QRcode+ Weibo
2. Facebook, Twitter, Linkedin.

Industry/Entity Type

Investment

```html
<!DOCTYPE html>
<html lang="en">
<head>
<meta charset="utf-8">
<title>Valdo Capital</title>
<link href="https://fonts.googleapis.com/css2?family=Open+Sans:wght@300;400;600&family=Raleway:wght@500;600;700&family=Ubuntu:wght@300;400;500&display=swap" rel="stylesheet">
<style>
  :root {
    --night-deep: #0b1526;
    --night-mid: #1d3556;
    --city-glow: #6a5a52;
    --harbour: #2c5a86;
    --white: #ffffff;
    --ink: #222222;
    --muted: #555555;
    --accent: #29aaf0;
    --panel: rgba(240, 240, 242, 0.93);
    --tab-brown: #4a3a2e;
    --footer-text: #a9b0ba;
    --divider: rgba(255, 255, 255, 0.45);
  }
  * { box-sizing: border-box; margin: 0; padding: 0; }
  html, body { width: 1200px; height: 984px; overflow: hidden; }
  body {
    position: relative;
    font-family: "Ubuntu", sans-serif;
    color: var(--white);
    background: var(--night-deep);
  }
  .hero-backdrop {
    position: absolute; inset: 0;
    background:
      radial-gradient(ellipse 420px 300px at 640px 560px, rgba(214,150,80,0.45), transparent 70%),
      radial-gradient(ellipse 500px 200px at 250px 520px, rgba(120,160,210,0.45), transparent 70%),
      linear-gradient(180deg, var(--night-deep) 0%, var(--night-mid) 30%, var(--harbour) 52%, var(--city-glow) 66%, #241c1a 100%);
  }
  .diagonal-shade { position: absolute; inset: 0; }

  .site-header {
    position: absolute; left: 110px; top: 0; width: 980px; height: 95px;
    background: var(--white);
    box-shadow: 0 2px 6px rgba(0,0,0,0.3);
  }
  .brand {
    position: absolute; left: 16px; top: 22px;
    display: flex; align-items: center; gap: 14px;
    font-family: "Open Sans", sans-serif; font-weight: 400;
    font-size: 32px; color: var(--ink); letter-spacing: 0.5px;
  }
  .brand-mark { width: 46px; height: 46px; background: var(--accent); }
  .lang-switch {
    position: absolute; left: 788px; top: 23px;
    font-family: "Open Sans", sans-serif; font-size: 13px; color: var(--ink);
  }
  .lang-switch .current { text-decoration: underline; }
  .lang-switch .caret { font-size: 8px; color: #666; margin-left: 6px; }
  .social { position: absolute; left: 868px; top: 18px; display: flex; gap: 6px; }
  .social span {
    width: 27px; height: 27px; border-radius: 50%;
    background: linear-gradient(#f2f2f2, #d6d6d6);
    box-shadow: 0 1px 2px rgba(0,0,0,0.25);
  }
  .main-nav {
    position: absolute; right: 20px; top: 59px;
    display: flex; gap: 8px;
    font-family: "Open Sans", sans-serif; font-size: 13px;
  }
  .main-nav a {
    color: var(--ink); text-decoration: none; padding: 3px 9px 4px; border-radius: 2px;
  }
  .main-nav a + a { margin-left: 4px; }
  .main-nav a.active { background: var(--accent); color: var(--white); }

  .hero-copy { position: absolute; left: 115px; top: 236px; width: 470px; }
  .hero-copy .welcome {
    font-family: "Open Sans", sans-serif; font-weight: 300;
    font-size: 62px; line-height: 62px; color: #0e1420; letter-spacing: -2px;
  }
  .hero-copy h1 {
    font-family: "Open Sans", sans-serif; font-weight: 600;
    font-size: 62px; line-height: 64px; letter-spacing: -1px;
  }
  .hero-copy p {
    margin: 10px 0 0 4px; font-family: "Open Sans", sans-serif;
    font-size: 17px; line-height: 22px;
  }
  .read-more-link {
    display: inline-block; margin: 8px 0 0 4px;
    font-family: "Open Sans", sans-serif; font-size: 17px;
    color: var(--white); text-decoration: underline;
  }
  .read-more-link .tri { font-size: 9px; text-decoration: none; margin-left: 6px; color: #ccc; }

  .about-panel {
    position: absolute; left: 110px; top: 615px; width: 223px; height: 259px;
    background: var(--panel); color: var(--muted); padding: 18px 12px;
  }
  .about-panel h2 {
    font-family: "Raleway", sans-serif; font-weight: 600; font-size: 18px; color: var(--ink);
    margin-bottom: 6px;
  }
  .about-panel p { font-size: 12.5px; line-height: 20px; font-weight: 300; color: #444; margin-bottom: 14px; }
  .about-panel a { font-size: 12.5px; color: var(--ink); }
  .about-panel .tri { font-size: 8px; color: #999; margin-left: 6px; }

  .tab {
    position: absolute; top: 874px; width: 223px; height: 37px;
    background: var(--white); border-radius: 0 0 3px 3px;
    display: flex; align-items: center; justify-content: space-between;
    padding: 0 12px; font-family: "Raleway", sans-serif; font-weight: 600;
    font-size: 17px; color: var(--ink);
  }
  .tab.is-current { background: var(--tab-brown); color: var(--white); font-size: 19px; }
  .tab svg { width: 14px; height: 24px; }

  .services { position: absolute; left: 560px; top: 646px; width: 530px; }
  .services h2 { font-family: "Raleway", sans-serif; font-weight: 600; font-size: 19px; }
  .services > p { font-size: 12.5px; line-height: 17px; font-weight: 300; margin-top: 4px; padding-left: 2px; }
  .services hr { border: 0; border-top: 1px dotted var(--divider); margin: 13px 0 0 2px; }
  .service {
    position: absolute; top: 90px; width: 230px; display: flex; gap: 12px;
  }
  .service .icon { width: 48px; height: 52px; background: rgba(255,255,255,0.9); border-radius: 4px; flex: none; }
  .service h3 { font-family: "Raleway", sans-serif; font-weight: 600; font-size: 19px; margin-top: -2px; }
  .service p { font-size: 12.5px; line-height: 16px; font-weight: 300; margin-top: 4px; }
  .service a { display: block; font-size: 13px; color: #ddd; text-decoration: none; margin-top: 7px; font-weight: 500; }
  .carousel-arrow { position: absolute; top: 744px; width: 20px; height: 44px; }

  .site-footer {
    position: absolute; left: 0; top: 938px; width: 1200px; height: 46px;
    border-top: 1px dotted rgba(255,255,255,0.35);
    font-family: "Open Sans", sans-serif; font-size: 12.5px; color: var(--footer-text);
  }
  .site-footer .copy { position: absolute; left: 111px; top: 13px; }
  .site-footer .legal { position: absolute; right: 110px; top: 13px; }
</style>
</head>
<body>
  <div class="hero-backdrop" role="img" aria-label="Night skyline of a harbour city with lit towers and waterfront"></div>
  <svg class="diagonal-shade" width="1200" height="984" viewBox="0 0 1200 984" aria-hidden="true">
    <polygon points="1200,0 1200,984 330,984 1200,40" fill="rgba(8,10,18,0.55)"/>
  </svg>

  <header class="site-header">
    <div class="brand"><span class="brand-mark"></span>Valdo Capital</div>
    <div class="lang-switch"><span class="current">EN</span> &nbsp;|&nbsp; SP<span class="caret">▼</span></div>
    <div class="social" aria-label="Social links"><span></span><span></span><span></span></div>
    <nav class="main-nav">
      <a href="#" class="active">HOME</a>
      <a href="#">FINANCIAL PRODUCTS</a>
      <a href="#">TEAM</a>
      <a href="#">NEWS</a>
    </nav>
  </header>

  <section class="hero-copy">
    <div class="welcome">Welcome To</div>
    <h1>Valdo Capital</h1>
    <p>Lorem ipsum dolor sit amet, consectetur adipisicing elit, sed do eiusmod tempor incididunt ut labore et dolore magna aliqua..</p>
    <a class="read-more-link" href="#">Read More<span class="tri">▶</span></a>
  </section>

  <aside class="about-panel">
    <h2>About Us</h2>
    <p>Lorem ipsum dolor sit amet, consec-tetur adipisicing elit, sed do eius-mod tempor incididunt ut labore et dolore magna aliqua..</p>
    <p>Lorem ipsum dolor sit amet, consec-tetur adipisicing elit. labore et dolore magna aliqua..</p>
    <a href="#">Read More</a><span class="tri">▶</span>
  </aside>

  <section class="services">
    <h2>Our Services</h2>
    <p>Lorem ipsum dolor sit amet, consectetur adipisicing elit, sed do eiusmod tempor incididunt ut labore et dolore magna aliqua..</p>
    <hr>
    <div class="service" style="left:0">
      <div class="icon" role="img" aria-label="Finance service icon"></div>
      <div>
        <h3>Finance</h3>
        <p>Valdo Capital lorem ipsum dolor sit amet..</p>
        <a href="#">Read More ⟶</a>
      </div>
    </div>
    <div class="service" style="left:310px">
      <div class="icon" role="img" aria-label="Consultancy service icon"></div>
      <div>
        <h3>Consultancy</h3>
        <p>Valdo Capital lorem ipsum dolor sit amet..</p>
        <a href="#">Read More ⟶</a>
      </div>
    </div>
  </section>
  <svg class="carousel-arrow" style="left:524px" viewBox="0 0 20 44" aria-hidden="true"><polyline points="18,2 3,22 18,42" fill="none" stroke="rgba(200,200,200,0.5)" stroke-width="4"/></svg>
  <svg class="carousel-arrow" style="left:1106px" viewBox="0 0 20 44" aria-hidden="true"><polyline points="2,2 17,22 2,42" fill="none" stroke="#2f8fd0" stroke-width="4"/></svg>

  <a class="tab is-current" style="left:110px">About Us<svg viewBox="0 0 14 24"><polyline points="2,2 12,12 2,22" fill="none" stroke="#bbb" stroke-width="3"/></svg></a>
  <a class="tab" style="left:363px">What We Do<svg viewBox="0 0 14 24"><polyline points="2,2 12,12 2,22" fill="none" stroke="#111" stroke-width="3"/></svg></a>
  <a class="tab" style="left:615px">Our Blog<svg viewBox="0 0 14 24"><polyline points="2,2 12,12 2,22" fill="none" stroke="#111" stroke-width="3"/></svg></a>
  <a class="tab" style="left:868px">Who We Are<svg viewBox="0 0 14 24"><polyline points="2,2 12,12 2,22" fill="none" stroke="#111" stroke-width="3"/></svg></a>

  <footer class="site-footer">
    <span class="copy">Copyright © 2014 Valdo Capital. All Rights Reserved</span>
    <span class="legal">Privacy Policy &amp; Term of Uses</span>
  </footer>
</body>
</html>
```